Events publishing website

Have increased the budget for Coded website design. Thanks
-
We need a wordpress website for events publishing. The website will be using all different kinds of events (social, business, music etc). The website should allow user to submit the new events. the new events will be published after admin reviewed.
Key menu items & requirements
- New Events (1-show picture, short description & start/end date. User can view more details in another page. 2-have categories, such as locations, free/ticked, event type etc. 3 - allow user to share the events in social website)
- Event organizer list (show the full list and most popular event organizers. users can view the list by categories, similar to above)
- events establishments (allow user to publish events related informations such as equipments, venue informations etc)
- discussion forum
Key functions
-registration page (new users should fill name, location, normal users or event organizer, types of event organizer etc)
-allow user to change locations to view different events
-search function
The functions should be similar to the following, the design should not. The website should not look like a proper website.
http://www.plavorgatherings.example
Reason: Hi All, have extended few days to allow some changes to be made for current design. Thanks

```html
<!DOCTYPE html>
<html lang="en">
<head>
<meta charset="utf-8">
<title>Events – Contact Us</title>
<link href="https://fonts.googleapis.com/css2?family=Ubuntu:wght@300;400;500&display=swap" rel="stylesheet">
<style>
:root{
  --page-bg:#efeee6;
  --page-bg-light:#f7f6f0;
  --topbar:#111111;
  --teal:#3f7773;
  --teal-light:#5c928d;
  --teal-dark:#35655f;
  --brand:#2d6a63;
  --text:#4a4a4a;
  --muted:#7a7a7a;
  --line:#d3d3d3;
  --orange:#f0a21a;
  --white:#ffffff;
}
*{box-sizing:border-box;margin:0;padding:0}
html,body{width:966px;height:1200px;overflow:hidden}
body{position:relative;font-family:"Ubuntu",sans-serif;color:var(--text);
  background:radial-gradient(ellipse at 30% 25%,var(--page-bg-light) 0%,var(--page-bg) 60%)}
.abs{position:absolute}
.topbar{left:0;top:0;width:966px;height:28px;background:var(--topbar);display:flex;align-items:center;padding-left:27px;font-size:10px;color:var(--white);letter-spacing:.2px}
.topbar span.sep{margin:0 10px}
.logo{left:36px;top:58px;font-size:34px;font-weight:400;color:var(--brand);line-height:1}
.slogan{left:38px;top:94px;font-size:15px;font-weight:300;color:var(--brand)}
.account{top:52px;right:40px;display:flex;gap:18px;font-size:13px;color:var(--teal-dark)}
.account div{display:flex;align-items:center;gap:4px}
.search{left:670px;top:88px;width:276px;height:32px;display:flex;background:var(--white);border:1px solid #dcdcd4}
.search span{flex:1;padding:8px 10px;font-size:12px;color:#888}
.search b{width:32px;background:var(--orange);color:var(--white);font-weight:400;font-size:14px;display:flex;align-items:center;justify-content:center}
.nav{left:27px;top:137px;width:923px;height:53px;background:linear-gradient(var(--teal-light),var(--teal));display:flex;align-items:center;font-size:16px;font-weight:300;color:var(--white);border-bottom:2px solid #e8efee}
.nav div{height:53px;display:flex;align-items:center;padding:0 24px 0 33px;border-right:1px dashed rgba(255,255,255,.35)}
.nav div:last-child{border-right:none}
.banner{left:27px;top:192px;width:923px;height:285px;background:linear-gradient(90deg,#6f6a5f 0%,#8b8470 30%,#3a2418 50%,#c7461b 65%,#e89a28 80%,#4a2a18 100%)}
.arrow{top:302px;width:26px;height:40px;background:rgba(255,255,255,.9);display:flex;align-items:center;justify-content:center;color:#8a8a8a;font-size:18px}
.arrow.prev{left:27px;border-radius:0 20px 20px 0}
.arrow.next{left:929px;border-radius:20px 0 0 20px}
.panel{left:36px;top:485px;width:905px;height:413px;background:var(--white);border:1px solid #dedede}
.panel h1{position:absolute;left:13px;top:14px;font-size:24px;font-weight:400;color:var(--brand)}
.form-title{left:63px;top:557px;font-size:17px;color:var(--muted);font-weight:400}
.label{left:63px;font-size:12px;color:var(--text)}
.input{left:63px;width:231px;height:19px;border:1px solid #bdbdbd;background:var(--white)}
.submit{left:101px;top:834px;width:145px;height:22px;border-radius:3px;background:linear-gradient(#8a8a8a,#2e2e2e);color:var(--white);font-size:13px;display:flex;align-items:center;justify-content:center}
.divider{left:449px;top:566px;width:1px;height:294px;background:var(--line)}
.map{left:470px;top:582px;width:238px;height:237px;border:1px solid #cfcfcf;background:linear-gradient(135deg,#e9e5dc,#dedad0)}
.contact-head{left:740px;top:695px;display:flex;align-items:center;gap:13px;font-size:17px;color:#666}
.contact-line{left:744px;font-size:11px;color:var(--text);white-space:nowrap}
.footer{left:28px;top:907px;width:923px;height:293px;background:linear-gradient(var(--teal-light),var(--teal) 70%,var(--teal-dark))}
.foot-title{top:925px;font-size:18px;color:var(--white);font-weight:300}
.links{left:71px;top:960px;width:518px}
.links .row{display:flex;height:26px;align-items:center;border-bottom:1px dashed rgba(255,255,255,.35);font-size:12px;color:var(--white)}
.links .row span{display:block}
.links .c1{width:104px;padding-left:1px}.links .c2{width:132px}.links .c3{width:132px}
.social{left:645px;top:957px;display:flex;gap:6px}
.social span{width:25px;height:25px;border-radius:50%;background:#f2f2f2;border:2px solid #d6e2e0}
.copy{left:47px;top:1105px;width:885px;height:44px;background:rgba(0,0,0,.12);border-radius:3px;display:flex;align-items:center;padding-left:18px;font-size:10px;color:var(--white)}
.copy i{font-style:normal;margin:0 5px}
</style>
</head>
<body>
<div class="abs topbar">EVENTS<span class="sep">|</span>NEWS EVENTS<span class="sep">|</span>SAVOR<span class="sep">|</span>EVENT INTERNATIONAL ART SERIES<span class="sep">|</span>PLAVOR EVENTS CALENDAR</div>

<div class="abs logo">Events</div>
<div class="abs slogan">your company slogan here</div>

<div class="abs account">
  <div><svg width="18" height="18" viewBox="0 0 18 18"><path d="M2 8h3v9H2zM6 8l4-7c2 0 2 2 1.5 4H16c1 0 1.5 1 1 2l-2 9H6z" fill="var(--teal-dark)"/></svg>SIGN UP</div>
  <div><svg width="16" height="20" viewBox="0 0 16 20"><path d="M4 9V5a4 4 0 0 1 8 0v4" stroke="var(--teal-dark)" stroke-width="2" fill="none"/><rect x="1" y="9" width="14" height="11" rx="1" fill="var(--teal-dark)"/></svg>LOGIN</div>
  <div><svg width="22" height="22" viewBox="0 0 22 22"><circle cx="11" cy="6" r="5" fill="var(--teal-dark)"/><path d="M1 22c0-7 4-10 10-10s10 3 10 10z" fill="var(--teal-dark)"/></svg>MEMBER</div>
</div>
<div class="abs search"><span>Enter Keyword here</span><b>Go</b></div>

<nav class="abs nav">
  <div>MAIN</div><div>POPULAR</div><div>EVENT ORGANIZER</div><div>FORUM</div><div>HELP</div><div>CONTACT US</div>
</nav>

<div class="abs banner" role="img" aria-label="Photo of a conference hall with rows of chairs, projection screens and orange stage lighting"></div>
<div class="abs arrow prev">&#10094;</div>
<div class="abs arrow next">&#10095;</div>

<section class="abs panel"><h1>Contact Us</h1></section>
<h2 class="abs form-title">Kindly post your valuable Suggestions &amp; Query</h2>
<div class="abs label" style="top:597px">Enter your Name</div>
<div class="abs input" style="top:615px"></div>
<div class="abs label" style="top:642px">Enter your Email</div>
<div class="abs input" style="top:662px"></div>
<div class="abs label" style="top:687px">Enter your Phone Number</div>
<div class="abs input" style="top:709px"></div>
<div class="abs label" style="top:732px">Add Your Comments Here:</div>
<div class="abs input" style="top:749px;height:44px"></div>
<div class="abs submit">Submit Query</div>

<div class="abs divider"></div>
<div class="abs map" role="img" aria-label="Street map showing the office location with a marker"></div>

<div class="abs contact-head">
  <svg width="24" height="24" viewBox="0 0 24 24"><rect width="24" height="24" rx="3" fill="#e3e3e3"/><path d="M8 5c1 0 2 3 2 4s-1 1-1 2 2 4 3 4 1-1 2-1 4 1 4 2-1 3-3 3C10 19 5 13 5 8c0-2 2-3 3-3z" fill="var(--white)"/></svg>
  Contact Details
</div>
<div class="abs contact-line" style="top:735px">#27 Fernway Rd,Lorem ipsum,</div>
<div class="abs contact-line" style="top:758px">Phone:+91 800 555 0190</div>
<div class="abs contact-line" style="top:780px">Tollfree: (006) 55501234</div>
<div class="abs contact-line" style="top:803px">E-mail: info@plavorgatherings.example</div>

<footer class="abs footer"></footer>
<div class="abs foot-title" style="left:68px">Quick Links</div>
<div class="abs links">
  <div class="row"><span class="c1">Hom page</span><span class="c2">Login</span><span class="c3">Support</span><span>Term &amp; Conditions of Use</span></div>
  <div class="row"><span class="c1">Events</span><span class="c2">FAQ</span><span class="c3">Add Events</span><span>Privacy Policy</span></div>
  <div class="row"><span class="c1">Popular</span><span class="c2">Login</span><span class="c3">Speical Events</span><span>Help</span></div>
  <div class="row" style="height:30px"><span class="c1">News</span><span class="c2">Forgot Password</span><span class="c3">Contact info</span><span></span></div>
</div>
<div class="abs foot-title" style="left:643px">Connect with Us</div>
<div class="abs social"><span></span><span></span><span></span></div>
<div class="abs copy">© 2012 Company Name<i>|</i>All right reserved<i>|</i>Policy Privacy</div>
</body>
</html>
```